Vesta PR Website

Vesta PR are a PR company with a requirement for a new website. In consultation with the client, we have defined a wireframe for a homepage to show content and functionality. A PDF of the wire frame is attached.
Current site http://www.vesta-pr.co.uk/
Updates
If you are using Stock Photography - please use iStock
Dear All
Unfortunately, my client didn't like any of the designs submitted.
I've uploaded 3 examples of the type of photography that will appear in the carousel as supplied by the client.
Target Market(s)
Business to Business/Professionals - high value clients
Number of Pages Required
1 page
Requirements
Must have
- Colour scheme is attached as a .ase file from Kuler and can be viewed on Kuler if you search for 'VESTA PR Palette'
Corporate Typeface is Futura Book - use of Cufon is OK
Current Logo to be reatainedCall 2 Action Buttons will be controlled via the CMS so a generic background may be useful for these.
Nice to have
- RSS feeds

```html
<!DOCTYPE html>
<html lang="en">
<head>
<meta charset="utf-8">
<title>Vesta PR — Home</title>
<link href="https://fonts.googleapis.com/css2?family=Jost:wght@400;500&family=Noto+Sans:wght@400;700&display=swap" rel="stylesheet">
<style>
:root{
  --teal-dark:#005a6e;
  --teal-text:#0b5a6c;
  --aqua:#9fd8d2;
  --aqua-light:#a7dfd8;
  --aqua-text:#7fd6d6;
  --ink:#111;
  --white:#fff;
  --grey-line:#bcbcbc;
}
*{margin:0;padding:0;box-sizing:border-box}
html,body{width:1183px;height:1200px;overflow:hidden;background:var(--white)}
body{position:relative;font-family:"Noto Sans",Verdana,sans-serif;color:var(--ink)}
.abs{position:absolute}
.futura{font-family:"Jost",sans-serif;font-weight:400}

/* header */
.brand{left:95px;top:28px;font-family:"Jost",sans-serif;font-weight:400;font-size:40px;color:var(--teal-dark)}
.contact-social{right:82px;top:26px;display:flex;align-items:center;gap:22px;font-size:12px;font-weight:700;color:var(--teal-dark)}
.contact-social .label{color:#124;letter-spacing:1px;font-size:11px}
.callout{right:80px;top:58px;font-size:26px;color:var(--teal-dark)}

/* nav */
.nav{left:0;top:100px;width:1183px;height:53px;background:var(--teal-dark)}
.nav ul{list-style:none;display:flex;align-items:center;height:53px;padding-left:134px}
.nav li{font-family:"Jost",sans-serif;font-size:17.5px;color:var(--white);display:flex;align-items:center}
.nav li+li::before{content:"|";margin:0 17px}
.nav .home{background:linear-gradient(#4a4a4a,#1c1c1c);height:53px;padding:0 20px;position:relative;margin-right:10px}
.nav .home::after{content:"";position:absolute;left:50%;bottom:-9px;margin-left:-9px;border:9px solid transparent;border-bottom:0;border-top-color:#1c1c1c}
.nav .home + li::before{content:none}

/* hero */
.hero{left:0;top:153px;width:1183px;height:278px;background:radial-gradient(ellipse at 40% 40%,#a9ddd8,var(--aqua) 70%,#93cfc9)}
.services{left:89px;top:174px;list-style:none}
.services li{font-family:"Jost",sans-serif;font-size:24px;color:var(--teal-text);height:50px;line-height:38px;padding-left:10px}
.services li.active{background:var(--teal-dark);color:var(--white);border:2px solid #0a1a22;border-radius:3px;width:276px;height:36px;line-height:31px;margin-bottom:14px;padding-left:8px}
.hero-curve{left:430px;top:153px}
.hero-title{left:470px;top:174px;font-size:31px;color:var(--teal-text)}
.hero-copy{left:474px;top:224px;width:425px;font-size:12.5px;line-height:19px}
.hero-copy p+p{margin-top:19px}
.view-more{left:474px;top:392px;font-size:12px;font-weight:700;color:var(--teal-dark);text-decoration:underline}
.hero-photo{left:920px;top:178px;width:182px;height:227px;border:3px solid var(--white);background:linear-gradient(160deg,#f3f3f3,#d9c8b8 55%,#2a2a2a)}

/* main */
.welcome{left:98px;top:462px;font-size:38px;color:var(--teal-text)}
.intro{left:98px;top:532px;width:630px;font-size:12.5px;line-height:18.7px}
.intro p+p{margin-top:18.7px}
.divider-v{border-left:1px dotted #999}
.card{width:287px;height:218px;border:1px solid var(--grey-line);border-radius:6px;background:linear-gradient(#fff,#dcdcdc)}
.card h2{position:absolute;left:16px;top:18px;font-family:"Jost",sans-serif;font-weight:400;font-size:25px;color:var(--ink)}
.card .body{position:absolute;left:18px;top:70px;width:250px;font-size:12.5px;line-height:15px}
.card .body p+p{margin-top:15px}
.card .thumb{position:absolute;right:22px;top:48px;width:81px;height:84px;background:linear-gradient(160deg,#e8e8e8,#b49680 60%,#3a3a3a)}
.card .narrow{width:160px}
.cta{left:826px;width:242px;height:70px;background:linear-gradient(#0f7f92,#005566);border:4px solid #0a0f12;display:flex;align-items:center;justify-content:center;font-family:"Jost",sans-serif;font-size:37px;color:var(--aqua-text)}

/* footer */
.footer{left:0;top:1008px;width:1183px;height:150px;background:var(--aqua-light)}
.footer-links{list-style:none;font-size:11.5px;font-weight:700;letter-spacing:1px;color:var(--teal-dark);line-height:18.7px}
.enews{left:843px;top:1026px;font-size:23px;font-weight:700;color:var(--teal-dark)}
.email-field{left:843px;top:1066px;width:235px;height:35px;background:var(--white);border:1px solid var(--teal-dark);font-size:12.5px;font-weight:700;letter-spacing:1px;color:var(--teal-dark);padding:9px 8px}
.subscribe{left:843px;top:1114px;width:107px;height:26px;border-radius:4px;background:linear-gradient(#137a8c,#005566);color:var(--white);font-family:"Jost",sans-serif;font-size:18px;text-align:center;line-height:26px}
.legal-bar{left:0;top:1158px;width:1183px;height:42px;background:var(--teal-dark);color:var(--white);font-size:11.5px;font-weight:700;letter-spacing:.5px;text-align:right;padding:19px 83px 0 0}
</style>
</head>
<body>

<header>
  <div class="abs brand">Vesta PR</div>
  <div class="abs contact-social">
    <span class="label">Email Us:</span>
    <span>Callwave</span><span>Chirper</span><span>Friendbook</span>
  </div>
  <div class="abs callout futura">Call us now 0141 555 0199</div>
</header>

<nav class="abs nav">
  <ul>
    <li class="home">Home</li>
    <li>Vesta Services</li>
    <li>Press Office</li>
    <li>Vesta Case Studies</li>
    <li>Vesta People</li>
    <li>Blog</li>
    <li>Vesta News</li>
    <li>Contact Us</li>
  </ul>
</nav>

<section class="abs hero"></section>
<svg class="abs hero-curve" width="40" height="278" viewBox="0 0 40 278"><path d="M32 0 Q-10 140 22 278" fill="none" stroke="#005a6e" stroke-width="2.5"/></svg>
<ul class="abs services">
  <li class="active">Online Public Relations</li>
  <li>Media Relations</li>
  <li>Consumer Campaigns</li>
  <li>Crisis Public Relations</li>
  <li>Internal Communications</li>
</ul>
<h1 class="abs hero-title futura">Online Public Relations</h1>
<div class="abs hero-copy">
  <p>Lorem Ipsum is simply dummy text of the printing and typesetting industry. Lorem Ipsum has been the industry's standard dummy text ever since the 1500s.</p>
  <p>When an unknown printer took a galley of type and scrambled it to make a type specimen book. It has survived not only five centuries, but also the leap into electronic typesetting, remaining essentially unchanged.</p>
</div>
<a class="abs view-more">View More</a>
<div class="abs hero-photo" role="img" aria-label="Portrait photo of a smiling team member"></div>

<main>
  <h2 class="abs welcome futura">Welcome to Vesta PR</h2>
  <div class="abs intro">
    <p>Vesta Public Relations is one of Scotland’s leading independent agencies. Founded in 2000, we were determined to create a public relations service with a real difference – hence the name.</p>
    <p>Vesta Public Relation's trademark is a fresh, creative and hard working approach to public relations. It is an approach that secures real results for our clients.</p>
    <p>We are an agency with intelligence, integrity and imagination offering a comprehensive, results driven public relations service covering traditional and online public relations strategy and support.</p>
  </div>

  <div class="abs divider-v" style="left:761px;top:475px;height:500px"></div>
  <div class="abs divider-v" style="left:406px;top:732px;height:238px"></div>

  <article class="abs card" style="left:96px;top:738px">
    <h2>Client News</h2>
    <div class="body">
      <p>Phasellus sapien ipsum, interdum ut dapibus in, hendrerit nec nulla. Donec</p>
      <p>egestas scelerisque metus, nec placeratlectus ultrices ac. Nam sodales mollis euismod. Mauris ornare viverra dignissim.</p>
    </div>
  </article>

  <article class="abs card" style="left:434px;top:738px">
    <h2>Blog Entry</h2>
    <div class="thumb" role="img" aria-label="Author portrait photo"></div>
    <div class="body">
      <p class="narrow">Phasellus sapien ipsum, interdum ut dapibus in, hendrerit nec nulla Donec.</p>
      <p>egestas scelerisque metus, nec placeratlectus ultrices ac. Nam sodales mollis euismod. Mauris ornare viverra dignissim.</p>
    </div>
  </article>

  <svg class="abs" style="left:935px;top:476px" width="26" height="34" viewBox="0 0 26 34"><path d="M2 2l11 11 11-11v8l-11 11-11-11z M2 14l11 11 11-11v8l-11 11-11-11z" fill="#8a8a8a"/></svg>
  <div class="abs cta" style="top:513px">C2A Button</div>
  <svg class="abs" style="left:935px;top:594px" width="26" height="34" viewBox="0 0 26 34"><path d="M2 2l11 11 11-11v8l-11 11-11-11z M2 14l11 11 11-11v8l-11 11-11-11z" fill="#8a8a8a"/></svg>
  <div class="abs cta" style="top:631px">C2A Button</div>
  <svg class="abs" style="left:935px;top:712px" width="26" height="34" viewBox="0 0 26 34"><path d="M2 2l11 11 11-11v8l-11 11-11-11z M2 14l11 11 11-11v8l-11 11-11-11z" fill="#8a8a8a"/></svg>
  <div class="abs cta" style="top:749px">C2A Button</div>
  <svg class="abs" style="left:938px;top:829px" width="26" height="34" viewBox="0 0 26 34"><path d="M2 2l11 11 11-11v8l-11 11-11-11z M2 14l11 11 11-11v8l-11 11-11-11z" fill="#8a8a8a"/></svg>
  <div class="abs cta" style="top:867px;left:829px">C2A Button</div>
</main>

<footer>
  <div class="abs footer"></div>
  <ul class="abs footer-links" style="left:108px;top:1026px">
    <li>Online Public Relations</li>
    <li>Media Relations</li>
    <li>Consumer Campaigns</li>
    <li>Crisis Public Relations</li>
    <li>Internal Communications</li>
  </ul>
  <ul class="abs footer-links" style="left:366px;top:1026px">
    <li>Subscribe to RSS Feed</li>
    <li>Our Friendbook page</li>
    <li>Link Three</li>
    <li>Link Four</li>
  </ul>
  <div class="abs enews">E-News Sign-up</div>
  <div class="abs email-field">Email Address</div>
  <div class="abs subscribe">Subscribe</div>
  <div class="abs legal-bar">© Copyright Notice | Site Credit | Legal</div>
</footer>

</body>
</html>
```